RTavenor Business Cards & Letterhead

I have a logo but need a design for some new business cards. We are a Design-Build Firm that specializes in the design and construction of commercial projects.
the cards need to be professional. no cartoon stuff.
i would like to have the cards in AI format so I can update the card as needed. Logo is provided.
Our Address is: 4187 Marlowe Ct. Apex, North Carolina 27614

```html
<!DOCTYPE html>
<html lang="en">
<head>
<meta charset="utf-8">
<title>RTavenor Business Card</title>
<link href="https://fonts.googleapis.com/css2?family=Roboto:wght@400;700&display=swap" rel="stylesheet">
<style>
  :root {
    --bg: #3b3b3b;
    --card-top: #525252;
    --card-bottom: #3a3a3a;
    --blue: #0a6aa3;
    --blue-light: #0a7ab8;
    --blue-deep: #005a8e;
    --text: #ffffff;
    --rule: #6a6a6a;
  }
  * { margin: 0; padding: 0; box-sizing: border-box; }
  html, body { width: 1200px; height: 1200px; overflow: hidden; }
  body {
    background: var(--bg);
    font-family: "Roboto", Arial, sans-serif;
    color: var(--text);
    position: relative;
  }
  .card {
    position: absolute;
    left: 262px;
    width: 685px;
    height: 392px;
    border-radius: 20px;
    overflow: hidden;
  }
  .card-front {
    top: 165px;
    background: linear-gradient(180deg, var(--card-top) 0%, var(--card-bottom) 55%, var(--card-bottom) 100%);
  }
  .card-front .edge-band {
    position: absolute;
    left: 0; right: 0; bottom: 0;
    height: 16px;
    background: linear-gradient(90deg, var(--blue-deep), var(--blue-light) 50%, var(--blue-deep));
  }
  .brand {
    position: absolute;
    left: 77px;
    top: 196px;
    transform: translateY(-50%);
    display: flex;
    align-items: center;
    gap: 8px;
  }
  .brand-square {
    width: 26px; height: 26px;
    background: var(--blue-light);
  }
  .brand-name {
    font-weight: 700;
    font-size: 38px;
    letter-spacing: 0.5px;
    color: var(--text);
    line-height: 1;
  }
  .divider {
    position: absolute;
    left: 365px;
    top: 108px;
    width: 1px;
    height: 180px;
    background: var(--rule);
  }
  .details {
    position: absolute;
    left: 385px;
    top: 106px;
  }
  .person-name {
    font-weight: 700;
    font-size: 24px;
    color: var(--blue-light);
    line-height: 1.1;
  }
  .person-title {
    font-size: 15.5px;
    line-height: 1.3;
    margin-top: 1px;
  }
  .address {
    font-size: 17px;
    line-height: 21px;
    margin-top: 9px;
  }
  .contacts {
    list-style: none;
    margin-top: 8px;
  }
  .contacts li {
    display: flex;
    align-items: center;
    font-size: 17px;
    line-height: 20.5px;
  }
  .contacts svg {
    width: 14px; height: 14px;
    margin-right: 12px;
    fill: var(--blue-light);
    flex: none;
  }
  .card-back {
    top: 653px;
    background: radial-gradient(ellipse at 50% 40%, var(--blue-light) 0%, #0668a0 45%, var(--blue-deep) 100%);
    display: flex;
    align-items: center;
    justify-content: center;
  }
  .back-brand {
    display: flex;
    align-items: center;
    gap: 14px;
  }
  .back-brand .brand-square {
    width: 40px; height: 40px;
    background: var(--text);
  }
  .back-brand .brand-name {
    font-size: 58px;
  }
</style>
</head>
<body>
  <section class="card card-front">
    <div class="brand">
      <span class="brand-square"></span>
      <span class="brand-name">RTAVENOR</span>
    </div>
    <div class="divider"></div>
    <div class="details">
      <p class="person-name">Daniel Whitcombe</p>
      <p class="person-title">Managing Director</p>
      <p class="address">4187 Marlowe Ct. Apex<br>North Carolina 27614</p>
      <ul class="contacts">
        <li><svg viewBox="0 0 24 24"><path d="M6.6 10.8a15 15 0 0 0 6.6 6.6l2.2-2.2c.3-.3.7-.4 1-.2 1.1.4 2.3.6 3.6.6.6 0 1 .4 1 1V20c0 .6-.4 1-1 1A17 17 0 0 1 3 4c0-.6.4-1 1-1h3.5c.6 0 1 .4 1 1 0 1.3.2 2.5.6 3.6.1.3 0 .7-.2 1z"/></svg>919-555-0142</li>
        <li><svg viewBox="0 0 24 24"><path d="M7 1h10a2 2 0 0 1 2 2v18a2 2 0 0 1-2 2H7a2 2 0 0 1-2-2V3a2 2 0 0 1 2-2zm0 3v15h10V4z"/></svg>919-555-0187</li>
        <li><svg viewBox="0 0 24 24"><path d="M2 5h20v14H2zm2 2v.5l8 5 8-5V7z"/></svg>info@rtavenor.com</li>
        <li><svg viewBox="0 0 24 24"><path d="M12 2a10 10 0 1 0 0 20 10 10 0 0 0 0-20zm-1 17.9A8 8 0 0 1 4.2 10L9 15v1a2 2 0 0 0 2 2zm6.9-2.5A2 2 0 0 0 16 16h-1v-3a1 1 0 0 0-1-1H8v-2h2a1 1 0 0 0 1-1V7h2a2 2 0 0 0 2-2v-.4a8 8 0 0 1 2.9 12.8z"/></svg>www.rtavenor.com</li>
      </ul>
    </div>
    <div class="edge-band"></div>
  </section>

  <section class="card card-back">
    <div class="back-brand">
      <span class="brand-square"></span>
      <span class="brand-name">RTAVENOR</span>
    </div>
  </section>
</body>
</html>
```